Business Card for premium dental clinic

We are a premium dental clinic based in Brasov, Romania with more than 15 year on the market, providing quality dental treatment made by a team of more specialized dentists, working with modern equipment as a solution to beautiful and healthy teeth.

Our current logo for the clinic use 2 square with colors black and gold - dr Ternisu - Aurelia, using family fonts Bodoni, Myriad Pro and Segoe Print.
Depending on the printing we used some gold CMYK background or gold foil picture background or a gold gradient.
We want a business card:
- eye catching business card
- distinguished business card
- premium design
- to keep the color scheme of black and gold
- to attract the customers to spent time reading the information
- modern concept

```html
<!DOCTYPE html>
<html lang="en">
<head>
<meta charset="utf-8">
<title>Aurelia dental clinic – business card</title>
<link rel="stylesheet" href="https://fonts.googleapis.com/css2?family=Roboto+Condensed:wght@300;400;700&family=Roboto:wght@400&display=swap">
<style>
  :root {
    --backdrop: #3a3a3c;
    --card-black: #232325;
    --gold-light: #f7d24a;
    --gold-mid: #e3b21f;
    --gold-deep: #b9860f;
    --white: #ffffff;
    --ink: #161616;
  }
  * { box-sizing: border-box; margin: 0; padding: 0; }
  html, body { width: 799px; height: 1200px; overflow: hidden; }
  body {
    background: var(--backdrop);
    font-family: "Roboto Condensed", "Arial Narrow", sans-serif;
    position: relative;
  }
  .card {
    position: absolute;
    left: 50px;
    width: 699px;
    height: 400px;
    background: var(--card-black);
    overflow: hidden;
    box-shadow: 0 14px 30px rgba(0,0,0,.45);
  }
  .card--front { top: 150px; }
  .card--back { top: 650px; }

  .gold-foil {
    background: linear-gradient(135deg, var(--gold-light) 0%, var(--gold-mid) 40%, var(--gold-deep) 70%, var(--gold-light) 100%);
  }

  /* front */
  .front-foil { position: absolute; left: 0; top: 0; width: 350px; height: 400px; }
  .name-plate {
    position: absolute; left: 38px; top: 128px; width: 312px; height: 122px;
    background: var(--white);
    display: flex; align-items: center; justify-content: center;
  }
  .doctor-name { color: var(--ink); font-weight: 300; font-size: 64px; line-height: 1; letter-spacing: -1px; white-space: nowrap; }
  .doctor-name .title { font-size: 40px; }
  .clinic-block { position: absolute; left: 390px; top: 150px; width: 280px; text-align: center; }
  .clinic-name { color: var(--white); font-weight: 700; font-size: 62px; line-height: 1; }
  .clinic-sub { color: var(--white); font-weight: 700; font-size: 40px; line-height: 1.2; margin-top: 10px; }

  /* back */
  .back-waves { position: absolute; inset: 0; width: 699px; height: 400px; }
  .back-brand { position: absolute; left: 70px; top: 60px; }
  .back-brand .clinic-name { font-size: 58px; text-align: left; }
  .back-brand .clinic-sub { font-size: 38px; margin-top: 6px; }
  .back-details { position: absolute; right: 40px; top: 150px; text-align: right; }
  .back-details .doctor-name { color: var(--gold-mid); font-size: 40px; }
  .back-details .doctor-name .title { font-size: 26px; }
  .address { font-family: "Roboto", Arial, sans-serif; color: var(--white); font-size: 16px; line-height: 1.3; margin-top: 10px; }
  .contact-list { position: absolute; right: 40px; bottom: 22px; list-style: none; font-family: "Roboto", Arial, sans-serif; color: var(--ink); font-size: 17px; line-height: 1.4; }
  .contact-list li { display: flex; align-items: center; justify-content: flex-end; gap: 10px; }
  .contact-list svg { width: 16px; height: 16px; fill: var(--ink); flex: none; }
</style>
</head>
<body>

<section class="card card--front" aria-label="Card front">
  <div class="front-foil gold-foil" role="img" aria-label="Gold foil texture"></div>
  <div class="name-plate">
    <p class="doctor-name"><span class="title">dr.</span>Ternisu</p>
  </div>
  <div class="clinic-block">
    <p class="clinic-name">Aurelia</p>
    <p class="clinic-sub">dental clinic</p>
  </div>
</section>

<section class="card card--back" aria-label="Card back">
  <svg class="back-waves" viewBox="0 0 699 400" role="img" aria-label="Gold foil waves">
    <defs>
      <linearGradient id="foil" x1="0" y1="0" x2="1" y2="1">
        <stop offset="0" stop-color="#f7d24a"/>
        <stop offset=".45" stop-color="#e3b21f"/>
        <stop offset=".75" stop-color="#b9860f"/>
        <stop offset="1" stop-color="#f2c93c"/>
      </linearGradient>
    </defs>
    <path d="M0,300 C120,270 260,320 400,300 S600,240 699,262 L699,400 L0,400 Z" fill="url(#foil)"/>
    <path d="M0,218 C110,230 230,300 420,290 C530,284 620,250 699,244" fill="none" stroke="url(#foil)" stroke-width="14" stroke-linecap="round"/>
    <path d="M0,252 C120,262 240,300 400,296" fill="none" stroke="url(#foil)" stroke-width="10" stroke-linecap="round"/>
  </svg>

  <div class="back-brand">
    <p class="clinic-name">Aurelia</p>
    <p class="clinic-sub">dental clinic</p>
  </div>

  <div class="back-details">
    <p class="doctor-name"><span class="title">dr.</span>Ternisu</p>
    <p class="address">57 Linden Row,<br>Maple Falls, US 204718</p>
  </div>

  <ul class="contact-list">
    <li>614-205-3390
      <svg viewBox="0 0 16 16" aria-hidden="true"><path d="M3 1h3l1 4-2 1c1 2 3 4 5 5l1-2 4 1v3c0 1-1 2-2 2C7 15 1 9 1 3c0-1 1-2 2-2z"/></svg></li>
    <li>hello@aureliadent.com
      <svg viewBox="0 0 16 16" aria-hidden="true"><path d="M1 3h14v10H1z M2 4l6 5 6-5" fill="none" stroke="#161616" stroke-width="1.5"/></svg></li>
    <li>www.aureliadent.com
      <svg viewBox="0 0 16 16" aria-hidden="true"><circle cx="8" cy="8" r="6.5" fill="none" stroke="#161616" stroke-width="1.5"/><path d="M1.5 8h13M8 1.5c-3 3-3 10 0 13M8 1.5c3 3 3 10 0 13" fill="none" stroke="#161616" stroke-width="1.2"/></svg></li>
  </ul>
</section>

</body>
</html>
```